We need a designer to help us represent our unique approach to creating lesson plans for digital learning. At the Coastal Workshop for Media Fluency, held in Providence RI this July 13 - 18, we'll use your design with 100 teachers and then put it online to reach hundreds of thousands more.

We have a draft visual of our model that we like - but it's not pretty (Since we are not designers, it looks a little clunky).

Please create a simple and attractive design in two versions: (1) one that we can use as a 1-page printed handout and (2) one that we can use where teachers can fill in sections and write ideas under each section of the graphic.

Why you should bid on this job? We're a leading provider of digital and media literacy curriculum resources with a huge international and national audience. Working with us will establish your expertise in the area of educational multimedia design.

Target Market(s)

Elementary and secondary teachers in public schools

Industry/Entity Type

Digital

Font styles to use
Sans Serif

Requirements
Must have
• TITLE : Digital Literacy Curriculum Framework

1 page version - suitable for use as a poster or 1-page flyer

Fillable form version - suitable for use as a handout with spaces for teachers to write

```html
<!DOCTYPE html>
<html lang="en">
<head>
<meta charset="utf-8">
<title>Digital Literacy Curriculum Framework</title>
<link rel="stylesheet" href="https://fonts.googleapis.com/css2?family=Source+Sans+3:wght@400;600;700&display=swap">
<style>
  :root {
    --paper: #ffffff;
    --ink-brown: #7a6440;
    --ring-olive: #e0ddb0;
    --divider: #ffffff;
    --self-peach: #fccb98;
    --learners-orange: #f9a54a;
    --community-sage: #a9c0b0;
    --context-yellow: #fcd462;
    --subject-coral: #f06a6a;
    --label-light: #ffffff;
  }
  html, body {
    margin: 0;
    padding: 0;
    width: 848px;
    height: 1200px;
    overflow: hidden;
    background: var(--paper);
  }
  .framework-sheet {
    display: block;
    width: 848px;
    height: 1200px;
    font-family: "Source Sans 3", "Myriad Pro", Arial, sans-serif;
  }
  .framework-title {
    fill: var(--ink-brown);
    font-weight: 700;
    font-size: 19.5px;
    letter-spacing: 1px;
  }
  .domain-label {
    fill: var(--ink-brown);
    font-size: 13.5px;
    letter-spacing: 0.3px;
  }
  .axis-line {
    stroke: var(--ink-brown);
    stroke-width: 0.8;
  }
  .outer-ring {
    fill: var(--ring-olive);
    stroke: var(--ink-brown);
    stroke-width: 1;
  }
  .segment-divider {
    stroke: var(--divider);
    stroke-width: 1;
  }
  .segment-label {
    fill: var(--ink-brown);
    font-size: 13.5px;
    letter-spacing: 0.4px;
  }
  .quadrant-self { fill: var(--self-peach); }
  .quadrant-learners { fill: var(--learners-orange); }
  .quadrant-community { fill: var(--community-sage); }
  .quadrant-context { fill: var(--context-yellow); }
  .quadrant-label {
    fill: var(--label-light);
    font-size: 13.5px;
  }
  .subject-ring {
    fill: none;
    stroke: var(--ink-brown);
    stroke-width: 0.8;
  }
  .subject-core { fill: var(--subject-coral); }
  .subject-label {
    fill: var(--label-light);
    font-size: 13px;
  }
</style>
</head>
<body>
<svg class="framework-sheet" viewBox="0 0 595 842" xmlns="http://www.w3.org/2000/svg" role="img" aria-label="Digital Literacy Curriculum Framework diagram">
  <defs>
    <path id="outer-label-track" d="M 300 688 A 248 248 0 1 1 300 192 A 248 248 0 1 1 300 688"/>
    <path id="inner-label-track" d="M 300 566 A 126 126 0 1 1 300 314 A 126 126 0 1 1 300 566"/>
  </defs>

  <text class="framework-title" x="309" y="57" text-anchor="middle">DIGITAL LITERACY CURRICULUM FRAMEWORK</text>

  <g class="domain-labels">
    <text class="domain-label" x="62" y="106">PURPOSE</text>
    <text class="domain-label" x="470" y="110">ASSESMENT</text>
    <text class="domain-label" x="60" y="805">CONTENT</text>
    <text class="domain-label" x="465" y="810">PEDAGOGY</text>
  </g>

  <g class="axes">
    <line class="axis-line" x1="300" y1="90" x2="300" y2="840"/>
    <line class="axis-line" x1="0" y1="440" x2="595" y2="440"/>
  </g>

  <circle class="outer-ring" cx="300" cy="440" r="287"/>

  <g class="segment-dividers">
    <line class="segment-divider" x1="209.6" y1="316.7" x2="130.4" y2="208.7"/>
    <line class="segment-divider" x1="377.4" y1="308.1" x2="445.2" y2="192.6"/>
    <line class="segment-divider" x1="449.3" y1="473.5" x2="580.1" y2="502.8"/>
    <line class="segment-divider" x1="300" y1="593" x2="300" y2="727"/>
    <line class="segment-divider" x1="151.6" y1="477.2" x2="21.6" y2="509.7"/>
  </g>

  <g class="segment-labels">
    <text class="segment-label" text-anchor="middle"><textPath href="#outer-label-track" startOffset="50%">STANDARDS</textPath></text>
    <text class="segment-label" text-anchor="middle"><textPath href="#outer-label-track" startOffset="69.7%">WORK PRODUCTS</textPath></text>
    <text class="segment-label" text-anchor="middle"><textPath href="#outer-label-track" startOffset="88.2%">INSTRUCTIONAL STRATEGIES</textPath></text>
    <text class="segment-label" text-anchor="middle"><textPath href="#outer-label-track" startOffset="9.9%">TOOLS</textPath></text>
    <text class="segment-label" text-anchor="middle"><textPath href="#outer-label-track" startOffset="30.3%">TEXT</textPath></text>
  </g>

  <g class="quadrants">
    <path class="quadrant-self" d="M 300 440 L 147 440 A 153 153 0 0 1 300 287 Z"/>
    <path class="quadrant-learners" d="M 300 440 L 300 287 A 153 153 0 0 1 453 440 Z"/>
    <path class="quadrant-community" d="M 300 440 L 453 440 A 153 153 0 0 1 300 593 Z"/>
    <path class="quadrant-context" d="M 300 440 L 300 593 A 153 153 0 0 1 147 440 Z"/>
  </g>

  <g class="quadrant-labels">
    <text class="quadrant-label" text-anchor="middle"><textPath href="#inner-label-track" startOffset="38.7%">Self</textPath></text>
    <text class="quadrant-label" text-anchor="middle"><textPath href="#inner-label-track" startOffset="63.4%">Learners</textPath></text>
    <text class="quadrant-label" text-anchor="middle"><textPath href="#inner-label-track" startOffset="85.8%">Community</textPath></text>
    <text class="quadrant-label" text-anchor="middle"><textPath href="#inner-label-track" startOffset="10.8%">Context</textPath></text>
  </g>

  <g class="subject-hub">
    <circle class="subject-ring" cx="300" cy="437" r="64"/>
    <circle class="subject-core" cx="300" cy="437" r="57"/>
    <text class="subject-label" x="298" y="442" text-anchor="middle">SUBJECT</text>
  </g>
</svg>
</body>
</html>
```